Oil Field Service company needs professional business cards

Looking to clean up our current company business cards and look a little more professional. Brenwick Casing Services is a US based company that services the oil field. We deal with engineers, managers and oil rigs....................................................................................................................................................................................................................................................................................................................................................................................................

Target Market(s)

Oil and Gas professionals

Industry/Entity Type

Oil And Gas

Contact Information for Business Card

See attached photo as example

Font styles to use
Sans Serif

Colors
ec1f27

Requirements
Must have
• Company Logo, Name, Title, Cell, Office, Fax, Email.
• See attached photo
Nice to have
• External CRT, Internal CRT, Casing Crews, Torque Turn, Laydown Machine
Should not have
• Do not introduce any new pictures and keep it professional looking

```html
<!DOCTYPE html>
<html lang="en">
<head>
<meta charset="utf-8">
<title>Brenwick Casing Services – Business Card</title>
<link rel="stylesheet" href="https://fonts.googleapis.com/css2?family=Montserrat:wght@700;800&family=Open+Sans:ital,wght@0,400;0,600;0,700;1,400&display=swap">
<style>
  :root {
    --slate: #44525d;
    --red: #ec1f27;
    --white: #ffffff;
    --ink: #5b6168;
    --ink-strong: #3a3f44;
    --backdrop: #e9e7e3;
  }
  * { box-sizing: border-box; margin: 0; padding: 0; }
  html, body { width: 1200px; height: 950px; overflow: hidden; }
  body {
    background: var(--backdrop);
    font-family: "Open Sans", Arial, sans-serif;
    position: relative;
  }

  .card {
    position: absolute;
    border-radius: 4px;
    box-shadow: 0 10px 28px rgba(0,0,0,0.18);
    overflow: hidden;
  }

  /* Front: portrait contact card */
  .card-front {
    left: 70px; top: 160px;
    width: 360px; height: 630px;
    background: var(--white);
  }
  .name-band {
    position: absolute;
    left: 0; top: 62px;
    width: 100%; height: 92px;
    background: var(--slate);
    color: var(--white);
    text-align: center;
    padding-top: 22px;
  }
  .name-band .person-name {
    font-family: "Montserrat", Arial, sans-serif;
    font-weight: 800;
    font-size: 25px;
    letter-spacing: 0.5px;
    text-transform: uppercase;
    line-height: 1.1;
  }
  .name-band .person-title {
    font-family: "Montserrat", Arial, sans-serif;
    font-weight: 700;
    font-size: 13px;
    letter-spacing: 1px;
    text-transform: uppercase;
    margin-top: 6px;
  }
  .band-rule {
    position: absolute;
    left: 90px; width: 180px; height: 3px;
    background: var(--red);
  }
  .band-rule.top { top: 52px; }
  .band-rule.bottom { top: 163px; }

  .contact-list {
    position: absolute;
    left: 0; top: 200px;
    width: 100%;
    list-style: none;
    text-align: center;
  }
  .contact-item {
    height: 66px;
    display: flex;
    flex-direction: column;
    align-items: center;
  }
  .contact-item svg { width: 16px; height: 16px; fill: var(--red); margin-bottom: 6px; }
  .contact-item span {
    font-size: 16px;
    color: var(--ink);
  }
  .contact-item.is-mobile span { font-weight: 700; color: var(--ink-strong); }

  /* Back: landscape brand card */
  .card-back {
    left: 500px; top: 295px;
    width: 630px; height: 360px;
    background: var(--slate);
    color: var(--white);
  }
  .brand {
    position: absolute;
    left: 0; top: 92px;
    width: 100%;
    text-align: center;
    font-family: "Montserrat", Arial, sans-serif;
    font-weight: 800;
    color: var(--white);
  }
  .brand .brand-dot {
    display: inline-block;
    width: 18px; height: 18px;
    border-radius: 50%;
    background: var(--red);
    margin-right: 14px;
    vertical-align: middle;
    position: relative; top: -6px;
  }
  .brand .brand-name {
    font-size: 62px;
    letter-spacing: 1px;
    line-height: 1;
  }
  .brand .brand-line {
    display: block;
    font-size: 17px;
    letter-spacing: 6px;
    margin-top: 12px;
  }
  .services {
    position: absolute;
    left: 0; top: 242px;
    width: 100%;
    text-align: center;
    font-style: italic;
    font-size: 15px;
    line-height: 1.55;
    color: var(--white);
  }
</style>
</head>
<body>

  <section class="card card-front" aria-label="Business card front">
    <div class="band-rule top"></div>
    <header class="name-band">
      <h1 class="person-name">Cody Harlan</h1>
      <p class="person-title">Area Manager</p>
    </header>
    <div class="band-rule bottom"></div>

    <ul class="contact-list">
      <li class="contact-item">
        <svg viewBox="0 0 16 16" aria-hidden="true"><path d="M8 0a5.5 5.5 0 0 0-5.5 5.5C2.5 10 8 16 8 16s5.5-6 5.5-10.5A5.5 5.5 0 0 0 8 0zm0 8a2.5 2.5 0 1 1 0-5 2.5 2.5 0 0 1 0 5z"/></svg>
        <span>Millbrook, OK 73990</span>
      </li>
      <li class="contact-item">
        <svg viewBox="0 0 16 16" aria-hidden="true"><path d="M3.6 1l2.3 3.1-1.4 1.6c.9 2 2.5 3.6 4.6 4.6l1.6-1.4L14 11.4 12.6 14C6.5 13.8 2.2 9.5 2 3.4z"/></svg>
        <span>(555)201-4800</span>
      </li>
      <li class="contact-item is-mobile">
        <svg viewBox="0 0 16 16" aria-hidden="true"><path d="M4 0h8a1 1 0 0 1 1 1v14a1 1 0 0 1-1 1H4a1 1 0 0 1-1-1V1a1 1 0 0 1 1-1zm1 2v10h6V2zm3 11a1 1 0 1 0 0 2 1 1 0 0 0 0-2z"/></svg>
        <span>(555)318-2264</span>
      </li>
      <li class="contact-item">
        <svg viewBox="0 0 16 16" aria-hidden="true"><path d="M4 1h7l1 2v3H4zM1 7h14v6H1zm2 2v2h2V9zM3 14h10v1H3z"/></svg>
        <span>(555)201-4811</span>
      </li>
      <li class="contact-item">
        <svg viewBox="0 0 16 16" aria-hidden="true"><path d="M1 3h14v1L8 9 1 4zm0 2.5l7 5 7-5V13H1z"/></svg>
        <span>cody@brenwick.com</span>
      </li>
      <li class="contact-item">
        <svg viewBox="0 0 16 16" aria-hidden="true"><circle cx="8" cy="8" r="7"/><path d="M1 8h14M8 1c-3 3.5-3 10.5 0 14M8 1c3 3.5 3 10.5 0 14" stroke="#fff" stroke-width="1" fill="none"/></svg>
        <span>www.brenwick.com</span>
      </li>
    </ul>
  </section>

  <section class="card card-back" aria-label="Business card back">
    <div class="brand">
      <span class="brand-dot" aria-hidden="true"></span><span class="brand-name">BRENWICK</span>
      <span class="brand-line">CASING SERVICES</span>
    </div>
    <p class="services">
      External CRT | Internal CRT | Casing Crews<br>
      Torque Turn | Laydown Machine
    </p>
  </section>

</body>
</html>
```